Business Card for Coach - ready to print

Design Business Card ready to order prints www.lukasbrenner.coach

* An Overview / Background of the Business & Services
· Coaching
· Personal growth
* The Target Market / Audience you are trying to reach
· private person in different roles (self, familiy, business role)s
* Design Specifics; any preferences or ideas for Style, Colour, Imagery, etc
· See www.lukasbrenner.coach
· "simple" design
· (small) element of surprise / unusual element

* Information that will be placed in the Business Card
· Beratung und Coaching
· Address: Lukas Brenner, Mosering 42, CH-8312 Winterthur, Mobile +41 79 264 53 07
* Do you have an existing website or Facebook page where designers can learn more about your company?
· lukasbrenner.coach

Target Market(s)

private person in different roles (self, familiy, business role)

Industry/Entity Type

Life Coaching

Contact Information for Business Card

Lukas Brenner
Mosering 42
CH-8312 Winterthur

Mobile: +41 79 264 53 07
Email: lubr@alpimail.ch
www.lukasbrenner.coach

Font styles to use
Sans Serif

Colors

Designer to choose colors to be used in the design.

Requirements
Must have
• "simple" design
• element of surprise / unusual element
• Beratung & Coaching
• see www.lukasbrenner.coach for colors and so...
Nice to have
• TA Symbol (three rings on top of each other) - unsual presentation
• QR Code of Website (see if it fits in and still looks good).

```html
<!DOCTYPE html>
<html lang="de">
<head>
<meta charset="utf-8">
<title>Lukas Brenner – Visitenkarte</title>
<link rel="stylesheet" href="https://fonts.googleapis.com/css2?family=Montserrat:wght@400;500;700&display=swap">
<style>
  :root {
    --brand-red: #b51c2b;
    --brand-red-dark: #a5192a;
    --brand-orange: #ef8e1c;
    --card-white: #f2f2f2;
    --ink: #3a3a3a;
    --ring: #3d3d3d;
    --photo-grey: #8c9096;
    --page-bg: #dcdcdc;
  }
  * { box-sizing: border-box; margin: 0; padding: 0; }
  html, body {
    width: 1200px; height: 1021px; overflow: hidden;
    background: var(--page-bg);
    font-family: "Montserrat", sans-serif;
  }
  .canvas { position: relative; width: 1200px; height: 1021px; }
  .card {
    position: absolute; left: 260px; width: 680px; height: 440px;
    overflow: hidden; box-shadow: 0 6px 18px rgba(0,0,0,.18);
  }
  /* Front */
  .card-front {
    top: 45px;
    background: linear-gradient(160deg, var(--brand-red) 0%, var(--brand-red-dark) 100%);
    display: flex; flex-direction: column; align-items: center; justify-content: center;
    color: #fff;
  }
  .brand-mark { display: flex; align-items: center; gap: 14px; }
  .brand-mark .dot { width: 18px; height: 18px; background: #fff; }
  .brand-name { font-weight: 700; font-size: 44px; letter-spacing: 2px; }
  .brand-tagline { margin-top: 6px; font-weight: 500; font-size: 24px; letter-spacing: 1.5px; }
  /* Back */
  .card-back { top: 535px; background: var(--card-white); }
  .portrait {
    position: absolute; left: 56px; top: 70px; width: 250px; height: 250px;
    border-radius: 50%; border: 3px solid var(--ring); padding: 8px; background: var(--card-white);
  }
  .portrait-fill {
    width: 100%; height: 100%; border-radius: 50%;
    background: radial-gradient(circle at 50% 40%, #a6a9ad 0%, var(--photo-grey) 60%, #5d6570 100%);
  }
  .contact { position: absolute; left: 360px; top: 110px; color: var(--ink); }
  .contact-name { color: var(--brand-red); font-weight: 700; font-size: 26px; letter-spacing: 1px; }
  .contact-role { font-size: 20px; margin-top: 2px; letter-spacing: .5px; }
  .contact-address { font-size: 20px; margin-top: 22px; line-height: 1.3; letter-spacing: .5px; }
  .contact-list { list-style: none; margin-top: 16px; font-size: 20px; line-height: 1.35; letter-spacing: .5px; }
  .contact-list li { display: flex; align-items: center; gap: 8px; }
  .contact-list svg { width: 18px; height: 18px; flex: none; }
  .bottom-band { position: absolute; left: 0; bottom: 0; width: 100%; height: 24px; display: flex; }
  .band-red { background: var(--brand-red); }
  .band-orange { background: var(--brand-orange); }
  .band-gap { width: 5px; background: var(--card-white); }
</style>
</head>
<body>
<main class="canvas">
  <section class="card card-front">
    <div class="brand-mark">
      <span class="dot"></span>
      <span class="brand-name">LUKAS BRENNER</span>
    </div>
    <p class="brand-tagline">Beratung &amp; Coaching</p>
  </section>

  <section class="card card-back">
    <div class="portrait"><div class="portrait-fill" role="img" aria-label="Porträtfoto von Lukas Brenner"></div></div>
    <div class="contact">
      <h1 class="contact-name">LUKAS BRENNER</h1>
      <p class="contact-role">Beratung &amp; Coaching</p>
      <p class="contact-address">Mosering 42<br>CH-8312 Winterthur</p>
      <ul class="contact-list">
        <li>
          <svg viewBox="0 0 18 18" aria-hidden="true"><rect x="4" y="1" width="10" height="16" rx="2" fill="none" stroke="var(--brand-orange)" stroke-width="1.6"/><line x1="8" y1="14" x2="10" y2="14" stroke="var(--brand-orange)" stroke-width="1.6"/></svg>
          +41 79 264 53 07
        </li>
        <li>
          <svg viewBox="0 0 18 18" aria-hidden="true"><rect x="1" y="3.5" width="16" height="11" fill="none" stroke="var(--brand-orange)" stroke-width="1.6"/><polyline points="1,3.5 9,10 17,3.5" fill="none" stroke="var(--brand-orange)" stroke-width="1.6"/></svg>
          lubr@alpimail.ch
        </li>
        <li>
          <svg viewBox="0 0 18 18" aria-hidden="true"><g fill="none" stroke="var(--brand-orange)" stroke-width="1.4"><circle cx="9" cy="9" r="7.5"/><ellipse cx="9" cy="9" rx="3.2" ry="7.5"/><line x1="1.5" y1="9" x2="16.5" y2="9"/><line x1="3" y1="5" x2="15" y2="5"/><line x1="3" y1="13" x2="15" y2="13"/></g></svg>
          www.lukasbrenner.coach
        </li>
      </ul>
    </div>
    <div class="bottom-band">
      <span class="band-red" style="width:54%"></span>
      <span class="band-gap"></span>
      <span class="band-orange" style="flex:1"></span>
      <span class="band-gap"></span>
      <span class="band-red" style="width:8%"></span>
    </div>
  </section>
</main>
</body>
</html>
```